Tarvex Consulting

Hi,
I have my own network consulting business (just me)
and need to get a logo and business card design together,

Based in New Zealand,

Gareth Holloway
Unified Communications and Network Architect

/design engineer,
and would like this to be the basis for personal branding and company identity

• I have the basis for a optional logo - needs color -

```html
<!DOCTYPE html>
<html lang="en">
<head>
<meta charset="utf-8">
<title>Tarvex Consulting – Business Cards</title>
<link rel="stylesheet" href="https://fonts.googleapis.com/css2?family=Marcellus&family=Open+Sans:wght@400;600;700&display=swap">
<style>
  :root {
    --backdrop: #1c1c1c;
    --card-white: #ffffff;
    --card-shade: #eeeeee;
    --front-light: #6fcbe0;
    --front-mid: #3f86c8;
    --front-deep: #3a2b92;
    --brand-blue: #2f80c0;
    --brand-violet: #4a3aa8;
    --text-dark: #2b2b2b;
    --text-body: #3c3c3c;
    --icon-blue: #2f80c0;
  }
  * { margin: 0; padding: 0; box-sizing: border-box; }
  html, body { width: 1200px; height: 883px; overflow: hidden; background: var(--backdrop); }
  .sheet { position: relative; width: 1200px; height: 883px; }

  .card {
    position: absolute; width: 524px; height: 292px;
    border-radius: 20px; overflow: hidden;
    font-family: "Open Sans", sans-serif;
  }
  .card--front-a { left: 84px; top: 156px; }
  .card--front-b { left: 621px; top: 156px; }
  .card--back-a  { left: 86px; top: 465px; }
  .card--back-b  { left: 624px; top: 465px; }

  .card--front {
    background:
      radial-gradient(ellipse 70% 95% at 38% 70%, var(--front-light) 0%, var(--front-mid) 55%, var(--front-deep) 100%);
  }
  .card--back {
    background: linear-gradient(135deg, var(--card-white) 0%, var(--card-white) 60%, var(--card-shade) 100%);
  }

  .brand-mark { position: absolute; border-radius: 50%; }
  .card--front .brand-mark { left: 320px; top: 100px; width: 84px; height: 84px; background: var(--card-white); }
  .card--back .brand-mark {
    left: 355px; top: 150px; width: 66px; height: 66px;
    background: radial-gradient(circle at 40% 35%, #5fd0ec 0%, var(--brand-blue) 50%, var(--brand-violet) 100%);
  }

  .brand-name {
    position: absolute; right: 30px;
    font-family: "Marcellus", serif; letter-spacing: 0.2px; white-space: nowrap;
  }
  .card--front .brand-name { top: 236px; font-size: 25px; color: var(--card-white); }
  .card--back .brand-name { top: 246px; font-size: 20px; color: var(--text-dark); }

  .brand-tagline { position: absolute; right: 30px; white-space: nowrap; }
  .card--front .brand-tagline { top: 272px; font-size: 11.5px; color: var(--card-white); }
  .card--back .brand-tagline { top: 276px; font-size: 9.5px; color: var(--text-body); }

  .person { position: absolute; left: 27px; top: 38px; }
  .person__name { font-size: 18px; font-weight: 700; color: var(--brand-blue); line-height: 24px; }
  .person__role { font-size: 14.5px; color: var(--text-body); line-height: 20px; }

  .address { position: absolute; font-size: 12.5px; color: var(--text-body); line-height: 18px; }
  .card--back-a .address { left: 30px; top: 112px; }
  .card--back-b .address { left: 30px; top: 110px; }

  .contact-list { position: absolute; left: 30px; top: 160px; list-style: none; font-size: 12.5px; color: var(--text-body); }
  .contact-list li { display: flex; align-items: center; height: 19.5px; }
  .contact-list svg { width: 12px; height: 12px; margin-right: 7px; fill: var(--icon-blue); }

  .contact-lines { position: absolute; left: 30px; top: 132px; font-size: 12.5px; color: var(--text-body); line-height: 18px; }
  .contact-lines .label { color: var(--brand-blue); }
  .contact-lines .gap { display: inline-block; width: 8px; }
</style>
</head>
<body>
<main class="sheet">

  <section class="card card--front card--front-a">
    <div class="brand-mark"></div>
    <div class="brand-name">TARVEX CONSULTING</div>
    <div class="brand-tagline">Unified Communications and Network Architect</div>
  </section>

  <section class="card card--front card--front-b">
    <div class="brand-name">TARVEX CONSULTING</div>
    <div class="brand-tagline">Unified Communications and Network Architect</div>
  </section>

  <section class="card card--back card--back-a">
    <div class="person">
      <div class="person__name">Gareth Holloway</div>
      <div class="person__role">Design Engineer</div>
    </div>
    <div class="address">12 Marlow Lane,<br>London EC2R 4TP United Kingdom</div>
    <ul class="contact-list">
      <li><svg viewBox="0 0 12 12"><path d="M1 4c0-2 2-3 5-3s5 1 5 3l-2 1-1-2H4L3 5zM3 6h6l1 5H2z"/></svg>409 552 3184</li>
      <li><svg viewBox="0 0 12 12"><rect x="1" y="8" width="2" height="3"/><rect x="4" y="6" width="2" height="5"/><rect x="7" y="4" width="2" height="7"/><rect x="10" y="2" width="2" height="9"/></svg>409 552 3184</li>
      <li><svg viewBox="0 0 12 12"><path d="M1 3h10v7H1z M2 4v0.5l4 3 4-3V4z" fill-rule="evenodd"/></svg>gareth@tarvexconsulting.com</li>
      <li><svg viewBox="0 0 12 12"><circle cx="6" cy="6" r="5"/><path d="M1 6h10M6 1v10M3 3.5h6M3 8.5h6" stroke="#fff" stroke-width="0.8" fill="none"/></svg>www.tarvexconsulting.com</li>
    </ul>
    <div class="brand-mark"></div>
    <div class="brand-name">TARVEX CONSULTING</div>
    <div class="brand-tagline">Unified Communications and Network Architect</div>
  </section>

  <section class="card card--back card--back-b">
    <div class="person">
      <div class="person__name">Gareth Holloway</div>
      <div class="person__role">Design Engineer</div>
    </div>
    <div class="address">12 Marlow Lane,&nbsp; London EC2R 4TP United Kingdom</div>
    <div class="contact-lines">
      <div><span class="label">P.</span> 409 552 3184<span class="gap"></span><span class="label">M.</span> 409 552 3184</div>
      <div><span class="label">E.</span> gareth@tarvexconsulting.com</div>
      <div>www.tarvexconsulting.com</div>
    </div>
    <div class="brand-name">TARVEX CONSULTING</div>
    <div class="brand-tagline">Unified Communications and Network Architect</div>
  </section>

</main>
</body>
</html>
```